Brochure Design Project

We need a brochure for our acting school, website is
www.stagelarkhouse.com - It needs to reflect youth, vitality, and people's DREAMS coming true...colors should be red and black, but open to something new as well...the courses included should be
Players' Rapid Forge, Steady Stage Bundle, And The Mastery Track

Emphasis on Players' Rapid Forge is the short term intensity.
Steady Stage Bundle is the benefit of getting all the tools to look for acting work.
Mastery Track is becoming a pro, and if you are in another country, being provided with a visa to come to the U.S.

I have attached pictures and logos...I will submit the copy once there is a framework...the OLD brochure is attached as well...

Thank you...

Marlon

Reason: We would like to see a couple more ideas...

Reason: HI there designers! Thanks for your submissions. We are almost ready to pick a design. Thanks for the understanding.

Target Market(s)

18-35 year olds...fairly affluent, educated, American, European, or Australian

Industry/Entity Type

School

Requirements
Must have
• Make it fun, clean, clear, and NOT corporate.

```html
<!DOCTYPE html>
<html lang="en">
<head>
<meta charset="utf-8">
<title>Stagelark House – Programs Brochure</title>
<link href="https://fonts.googleapis.com/css2?family=Archivo+Black&family=Open+Sans:wght@400;600;700&display=swap" rel="stylesheet">
<style>
  :root{
    --red:#8e1b2b;
    --red-deep:#5e0f1b;
    --red-bright:#c8202f;
    --ink:#151515;
    --grey-light:#ececed;
    --grey-mid:#c9c9cc;
    --paper:#f5f5f6;
    --white:#ffffff;
    --stage:#f0f0f0;
  }
  *{box-sizing:border-box;margin:0;padding:0}
  html,body{width:1200px;height:862px;overflow:hidden;background:var(--stage)}
  body{font-family:"Open Sans",Arial,sans-serif}
  .canvas{position:relative;width:1200px;height:862px;overflow:hidden;background:var(--stage)}

  .spread{position:absolute;left:50px;top:140px;width:750px;height:580px;display:flex;box-shadow:0 6px 22px rgba(0,0,0,.18)}
  .panel{position:relative;width:250px;height:580px;overflow:hidden}
  .panel-bg{position:absolute;inset:0;width:100%;height:100%}
  .panel-content{position:relative;height:100%}

  .headline{font-family:"Archivo Black",Arial,sans-serif;text-transform:uppercase;line-height:1}
  .block-word{display:inline-block;background:var(--ink);color:var(--white);padding:2px 6px 0;margin-bottom:3px}

  .section-bar{position:absolute;left:0;right:0;height:24px;background:var(--ink);color:var(--white);
    font-family:"Archivo Black",Arial,sans-serif;font-size:11.5px;text-transform:uppercase;padding:6px 12px 0}
  .section-tag{position:absolute;right:10px;bottom:-8px;background:var(--red-bright);color:var(--white);
    font-family:"Open Sans",Arial,sans-serif;font-weight:700;font-size:6.5px;letter-spacing:.5px;padding:1px 5px}
  .copy{position:absolute;left:14px;right:14px;font-size:6.6px;line-height:1.5;text-align:justify}
  .copy p+p{margin-top:5px}
  .copy-light{color:var(--white)}
  .copy-dark{color:#333}

  .photo{position:absolute;left:14px;right:14px}
  .badge{position:absolute;width:22px;height:22px;background:var(--ink);border:2px solid var(--white)}

  .panel-intro{background:var(--grey-light)}
  .intro-title{position:absolute;left:14px;top:30px;font-size:30px}
  .programs-label{position:absolute;left:112px;top:134px;background:var(--red-bright);color:var(--white);
    font-weight:700;font-size:7px;letter-spacing:1px;padding:2px 8px;text-transform:uppercase}

  .cover{position:absolute;left:860px;top:140px;width:250px;height:580px;background:var(--paper);overflow:hidden;
    box-shadow:0 6px 22px rgba(0,0,0,.18)}
  .brand{position:absolute;top:38px;left:0;right:0;display:flex;align-items:center;justify-content:center;gap:7px;
    font-family:"Archivo Black",Arial,sans-serif;font-size:15px;color:#4a4a4a;text-transform:uppercase;letter-spacing:1px}
  .brand-dot{width:10px;height:10px;border-radius:50%;background:#4a4a4a}
  .cover-photo{position:absolute;left:16px;right:16px;top:130px;height:62px;background:linear-gradient(180deg,#3a3434 0%,#1a1616 100%)}
  .cover-title{position:absolute;left:16px;top:200px;font-size:50px}
  .cover-title .block-word{padding:4px 8px 0}
  .cover-sub{position:absolute;left:0;right:0;top:466px;text-align:right;padding-right:18px}
  .cover-sub .program{font-family:"Archivo Black",Arial,sans-serif;font-size:12.5px;color:var(--ink);text-transform:uppercase}
  .cover-sub .tagline{font-weight:600;font-size:12px;color:var(--red-bright);border-right:3px solid var(--red-bright);padding-right:5px;display:inline-block;margin-top:2px}
</style>
</head>
<body>
<div class="canvas">

  <section class="spread" aria-label="Brochure inside spread">

    <article class="panel panel-intro">
      <svg class="panel-bg" viewBox="0 0 250 580" preserveAspectRatio="none" aria-hidden="true">
        <polygon points="0,0 250,0 250,150 0,200" fill="#f3f3f4"/>
        <polygon points="0,180 250,140 250,360 0,400" fill="var(--red)"/>
        <polygon points="0,400 250,360 250,380 0,420" fill="var(--red-deep)"/>
        <polygon points="150,580 250,470 250,580" fill="var(--grey-mid)"/>
      </svg>
      <div class="panel-content">
        <h2 class="headline intro-title">
          <span class="block-word">What</span><br>
          <span class="block-word">We do</span><br>
          <span class="block-word">About it</span>
        </h2>
        <span class="programs-label">• Programs •</span>

        <span class="badge" style="right:16px;top:150px"></span>
        <div class="section-bar" style="top:176px;background:var(--red-deep)">Players' Rapid Forge I<span class="section-tag">4 weeks</span></div>
        <div class="copy copy-light" style="top:214px">
          <p>The Players' Rapid Forge I, created by Artistic Director Marlon Drayke, with over 1,200 graduates on StageList, offers an alternative to acting teacher evenings: full time, 30 minutes on your feet, daily actors' training. We acknowledge the 21st century by offering only the practical and useful elements of The Hale Technique and The Orlov Technique, as well as the practical application of all this to cold reading and scene study.</p>
          <p>The Players' Rapid Forge I is four weeks of daily classes, by the end of which you will know if acting is your life's work or just a passing fancy.</p>
        </div>

        <span class="badge" style="right:16px;top:356px"></span>
        <div class="section-bar" style="top:384px">Players' Rapid Forge II<span class="section-tag">8 weeks</span></div>
        <div class="copy copy-dark" style="top:422px">
          <p>The Army's Boot Camp prepares you for war; The Players' Rapid Forge II prepares you for a much tougher battle – Show Business; that's why it's eight glorious weeks of daily work. After Forge II, you will never again be able to return to civilian life, you are now an actor. Here you continue to learn and apply only the relevant aspects of the Hale and Orlov Techniques, you will learn true on-camera skills so that you can work on any type of shoot, and you will learn and APPLY business tools that will get you going in your career.</p>
        </div>
      </div>
    </article>

    <article class="panel" style="background:var(--red)">
      <svg class="panel-bg" viewBox="0 0 250 580" preserveAspectRatio="none" aria-hidden="true">
        <polygon points="0,0 250,0 250,40 0,70" fill="var(--red-deep)"/>
        <polygon points="0,300 250,270 250,300 0,330" fill="var(--red-deep)"/>
        <polygon points="0,520 250,470 250,580 0,580" fill="var(--red-deep)"/>
      </svg>
      <div class="panel-content">
        <div class="section-bar" style="top:30px">The Steady Stage Bundle<span class="section-tag">3 months</span></div>
        <div class="copy copy-light" style="top:66px">
          <p>There are those who come to Hollywood, manage to get an audition, go in hoping for the best, and fail miserably. While there is something to be said for that kind of moxie, there's also something to be said for knowing your craft. When you get one shot with a casting director, director or producer, be ready. The Steady Stage Bundle gives you everything you need to book the part, including a personalized way to market yourself. It leaves you with one thing: NO EXCUSES. So what are you waiting for?</p>
        </div>
        <div class="photo" role="img" aria-label="Photo: actor rehearsing a scene in front of a camera crew"
             style="top:176px;height:96px;background:radial-gradient(circle at 55% 45%,#6b5a52 0%,#2a2222 55%,#0f0c0c 100%)"></div>

        <div class="section-bar" style="top:290px">The Advanced Program<span class="section-tag">Ongoing</span></div>
        <div class="copy copy-light" style="top:326px">
          <p>Only auditioning, committed actors are invited to the Advanced Program. Why? Because we want to offer an intense experience in getting you in shape and in front of agents, managers and casting directors. During our ongoing course, you will gain a deep understanding of character and script analysis, as well as invaluable experience playing many different kinds of parts in all of the genres you might audition for in today's industry.</p>
        </div>
        <div class="photo" role="img" aria-label="Photo: group of students watching a scene on stage"
             style="top:432px;height:104px;background:radial-gradient(circle at 60% 30%,#7a7f86 0%,#2b2d31 50%,#0d0d0f 100%)"></div>
      </div>
    </article>

    <article class="panel" style="background:var(--red-deep)">
      <svg class="panel-bg" viewBox="0 0 250 580" preserveAspectRatio="none" aria-hidden="true">
        <polygon points="0,0 250,0 250,60 0,30" fill="var(--red)"/>
        <polygon points="0,440 250,380 250,580 0,580" fill="var(--grey-mid)"/>
        <polygon points="0,440 250,380 250,400 0,460" fill="var(--red)"/>
      </svg>
      <div class="panel-content">
        <div class="section-bar" style="top:30px">Mastery Track<span class="section-tag">18 months</span></div>
        <div class="copy copy-light" style="top:66px">
          <p>Designed for those who come to Los Angeles and are committed to turning their dream into reality, the Mastery Track gives you a daily routine of work on your craft, 22 hours a week, every week.</p>
          <p>Utilizing only the effective and updated elements of the Hale and Orlov Techniques, you will work with the finest teachers on camera and on stage. You will also learn and APPLY business tools, audition technique and self-marketing.</p>
          <p>At the end of the eighteen months you will receive a certificate of completion, something to be proud of.</p>
          <p>If you are an international student and you can qualify, the Mastery Track can help you obtain a visa. Contact us and we will do our best to arrange it for you.</p>
        </div>
        <div class="photo" role="img" aria-label="Photo: actors performing an emotional scene"
             style="top:300px;height:80px;background:radial-gradient(circle at 40% 50%,#5a4740 0%,#241a1a 60%,#0e0a0a 100%)"></div>
        <div class="headline" style="position:absolute;left:14px;top:474px;font-size:20px">
          <span class="block-word" style="font-size:10px">If not now,</span><br>
          <span class="block-word">When?</span>
        </div>
      </div>
    </article>
  </section>

  <article class="cover" aria-label="Brochure front cover">
    <svg class="panel-bg" viewBox="0 0 250 580" preserveAspectRatio="none" aria-hidden="true">
      <polygon points="0,0 250,0 250,120 0,160" fill="#fafafa"/>
      <polygon points="0,420 250,360 250,460 0,520" fill="var(--red)"/>
      <polygon points="0,520 250,460 250,580 0,580" fill="var(--red-deep)"/>
      <polygon points="0,470 250,410 250,470 0,530" fill="var(--paper)" opacity=".9"/>
    </svg>
    <div class="brand"><span class="brand-dot"></span>Stagelark House</div>
    <div class="cover-photo" role="img" aria-label="Photo: group of acting students posing together"></div>
    <h1 class="headline cover-title">
      <span class="block-word">If</span><br>
      <span class="block-word">Not</span><br>
      <span class="block-word">Now,</span><br>
      <span class="block-word" style="font-size:42px">When?</span>
    </h1>
    <div class="cover-sub">
      <div class="program">Players' Rapid Forge</div>
      <div class="tagline">Act on your dream</div>
    </div>
  </article>

</div>
</body>
</html>
```